Larkspur Talent IT Recruiting firm needs a business card design for Recruiters, Sourcers, and Account

We need business cards that allow us to change all contact info, names, titles (Recruiter, Sourcer, Account Manager, Director, CEO, etc) per person since we have three offices, in three cities, Phoenix, Austin, and Las Vegas. We do recruiting and contractors for IT positions (Developers, Architects, Software Engineers, Security Engineers, Help Desk, DBAs, PMs, Scrum Masters, etc.) Our client companies are very diverse from Meridian 100 to silicone Valley type start-ups.

So, while we what hip, techie, and quirky, it still needs to be professional. Primary color we use is blue, with silver as a secondary color.

Target Market(s)

IT, Technology

Industry/Entity Type

Business

Contact Information for Business Card

Company name: Larkspur Talent, Inc.
Website: www.larkspurtalent.example
Logos for Careerloop, Blipster, and Myriada

Name, Title, Office Number, Cell Number, email

Font styles to use
Serif
Sans Serif

Colors
0455a3
d5d5d5

Requirements
Nice to have
• The grey I selected below is not necessary - but, would like silver included. I included a card design (File 3: LTI early trial example.jpg) that I had started on. It's very rough, and not quite what we're looking for, but what we did like is the logo, big, maybe a bit faded, off center, goes out of frame, etc. Still looking for other ideas - you are the pros! But, just an idea of a design element we liked.

```html
<!DOCTYPE html>
<html lang="en">
<head>
<meta charset="utf-8">
<title>Larkspur Talent — Business Card</title>
<link rel="stylesheet" href="https://fonts.googleapis.com/css2?family=Questrial&display=swap">
<style>
  :root {
    --backdrop: #e4e4e4;
    --card: #f7f7f7;
    --card-shade: #e6e6e6;
    --blue: #0455a3;
    --blue-light: #1a8ad6;
    --blue-bright: #2aa3e6;
    --edge: #1d1d1d;
    --ink: #222222;
    --white: #ffffff;
  }
  * { box-sizing: border-box; margin: 0; padding: 0; }
  html, body { width: 1200px; height: 899px; overflow: hidden; }
  body {
    background: var(--backdrop);
    font-family: "Questrial", "Helvetica Neue", Arial, sans-serif;
    color: var(--ink);
    position: relative;
  }
  .card {
    position: absolute;
    left: 110px; top: 165px;
    width: 980px; height: 560px;
    background: radial-gradient(ellipse at 55% 35%, var(--white) 0%, var(--card) 45%, var(--card-shade) 100%);
    box-shadow: 0 18px 40px rgba(0,0,0,.25);
    overflow: hidden;
  }
  .card__panel { position: absolute; inset: 0; width: 100%; height: 100%; }
  .brand {
    position: absolute; left: 62px; top: 100px;
    font-family: "Questrial", "Helvetica Neue", Arial, sans-serif;
    font-size: 44px; letter-spacing: 3px;
    text-transform: uppercase;
    color: var(--blue);
    white-space: nowrap;
  }
  .contact {
    position: absolute; left: 62px; top: 300px;
    font-size: 19px; letter-spacing: .5px; line-height: 1.35;
  }
  .contact__address { margin-bottom: 16px; font-size: 21px; }
  .contact__list { list-style: none; }
  .contact__item { display: flex; align-items: center; gap: 12px; height: 33px; white-space: nowrap; }
  .contact__icon { width: 20px; height: 20px; fill: var(--ink); flex: none; }
  .person {
    position: absolute; right: 18px; top: 345px;
    width: 280px; text-align: center; color: var(--white);
    text-transform: uppercase; white-space: nowrap;
  }
  .person__name { font-size: 24px; letter-spacing: 1.5px; }
  .person__title { font-size: 17px; letter-spacing: 1.5px; margin-top: 4px; }
</style>
</head>
<body>
  <section class="card" aria-label="Larkspur Talent business card">
    <svg class="card__panel" viewBox="0 0 980 560" preserveAspectRatio="none" aria-hidden="true">
      <defs>
        <radialGradient id="panelBlue" cx="0.7" cy="0.35" r="0.8">
          <stop offset="0" stop-color="#2aa3e6"/>
          <stop offset="0.55" stop-color="#1a8ad6"/>
          <stop offset="1" stop-color="#0455a3"/>
        </radialGradient>
      </defs>
      <path d="M712 0 C 660 120 650 330 724 560 L 980 560 L 980 0 Z" fill="#1d1d1d"/>
      <path d="M722 0 C 672 120 664 330 736 560 L 980 560 L 980 0 Z" fill="url(#panelBlue)"/>
    </svg>

    <p class="brand">Larkspur Talent</p>

    <div class="contact">
      <p class="contact__address">412 Harbor Row, Suite 9<br>Austin TX</p>
      <ul class="contact__list">
        <li class="contact__item"><span class="contact__icon"></span>555 014 2290</li>
        <li class="contact__item">
          <svg class="contact__icon" viewBox="0 0 20 20"><path d="M5 3c1 0 2 3 2 4s-1 1.5-1 2 2 4 4 5c.5 0 1-1 2-1s4 1 4 2-1 3-3 3C8 18 2 12 2 6c0-2 2-3 3-3z"/></svg>
          555 014 2291</li>
        <li class="contact__item">
          <svg class="contact__icon" viewBox="0 0 20 20"><path d="M6 1h8a1 1 0 0 1 1 1v16a1 1 0 0 1-1 1H6a1 1 0 0 1-1-1V2a1 1 0 0 1 1-1zm1 2v12h6V3zm3 13a1 1 0 1 0 0 2 1 1 0 0 0 0-2z"/></svg>
          555 014 2292</li>
        <li class="contact__item">
          <svg class="contact__icon" viewBox="0 0 20 20"><path d="M5 2h7l3 3v4h2v9H3V9h2zm2 2v5h6V6h-2V4zm-2 8v2h2v-2zm4 0v2h2v-2zm4 0v2h2v-2z"/></svg>
          dwhitford@larkspurtalent.example</li>
        <li class="contact__item">
          <svg class="contact__icon" viewBox="0 0 20 20"><path d="M1 4h18v12H1zm2 2v.5l7 5 7-5V6l-7 5z"/></svg>
          www.larkspurtalent.example</li>
      </ul>
    </div>

    <div class="person">
      <p class="person__name">Daniel Whitford</p>
      <p class="person__title">Financial Advisor</p>
    </div>
  </section>
</body>
</html>
```